Website for a financial survey consultancy

WHO WE ARE
We're a niche HR consultancy specialising in salary comparison surveys for the financial asset management industry. We position ourselves as a small, highly responsive organisation with a strong personal relationship with each of our 50+ blue-chip clients.

WHAT WE DO
Our business is 80% surveys (= products), 20% consultancy (= services). The surveys are a set of online products which clients interact with to find the information they are interested in.

WHAT WE WANT
We are completely revising our existing marketing website and need a new up-to-date look and feel for the site. We want you to design 2 web pages
- Home page
- Internal content page

More details below in Must Have Priorities.

REFERENCE SITES
- www.veltramoor.com - nice background image
- www.plimweather.com - ignoring the animations
- www.gasketvale.com
- www.quorbin.com - clean, fresh, styly but prob not corporate enough
- www.dulveropinex.com - spacious, beautiful, slightly dated tho
- www.tambly.co.uk - ignore the colours. Like the simplicity, larger font size (although want to stick with sans-serif fonts for main content)

DELIVERABLES
The final designs should be delivered as one or more PSD files with clearly named layers. All design elements and treatments should be separated out, for example use adjustment layers rather than applied (and subsequently irreversible) adjustments, strokes, shading, etc.

WHAT NEXT
I'll be monitoring the contest every day and can respond to questions fast. You can IM me on Chatterlyne or QBX.

Reason: Hi folks,

I am extending the deadline to this project as I am travelling this week and therefore will not be able to make a final decision until next Monday. I will try and provide further feedback over the course of this week but I am only going to be online occasionally so be prepared to wait a few days for a reply from me.

Thanks for all the designs so far.

Tobias

Target Market(s)

In order of importance, most important first

1. Potential customers - UK & US financial industry HR professionals, short on time. Heard about us already, want to find out more about what we do, confirm relevance for their needs. Core goal - establish credibility: are we properly resourced, will we be around for years to come, are we *real*.

2. Existing customers - UK & US financial industry professionals, short on time, under pressure, want results quickly, minimum faff, expect high quality, slickly presented information. Primary action: login and use surveys.

3. Industry professionals/researchers - probably arriving through blog content, looking to browse and hoover information. Valuable for their ability to spread awareness of who we are amongst their peers.

Industry/Entity Type

Financial

Requirements
Must have
• GENERAL
Style cues - Corporate, professional, financial, stylish, slick, clean, spacious, light
Size - standard 960px grid

NAVIGATION
- [ Home | About us | Surveys | Consulting | Blog ]
- Sub-nav (roll-over dropdown) on About Us, Surveys & Consulting

ALL PAGES
- Site navigation
- Client login (on screen permanently or link to ajaxy in-page pop-up)
- Footer section
- Existing logo (attached)* - this is obviously an important reference point in the design, esp colour

HOME PAGE
- Communicate (link thru to?) survey/consulting split
- Large photo(s)/backdrop (2-3 interchangeable options ideally). Please consider what rights agreement will be necessary for any photos you include in your design.
- Possibly bigger more prominent version of logo
- Strap line/sentence - "Focussed data is the key to success"
- 3 recent blog posts (should look good with and without blog post images)
- Free downloadable PDF research report + supporting blurb

INTERNAL PAGE
- Page title
- Content - typical page will be less than one screenfull
- Level 1 sub-heading
- Level 2 sub-heading
- Bulleted list
- Content supporting image (any image will do - interested in placement, borders (if any), spacing, caption, etc)
- 'Do something' button

* Note: there is some internal debate about this logo at the moment. Some (me) are keen for it to change, some (not me!) are not. If you have an web page design idea/concept that requires an evolution of the logo, go ahead and evolve it. We can explore this further in the design process as necessary, but don't sweat it.
Nice to have
• Values to communicate
- Knowledgeable
- Professional
- Secure
- Personal
- Experienced
- Financial industry specific
- Accurate
- Reliable
Should not have
• - Search box
- Social media links, other than RSS feed button (discrete)

```html
<!DOCTYPE html>
<html lang="en">
<head>
<meta charset="utf-8">
<title>Halvorn — Focussed data is the key to success</title>
<link rel="stylesheet" href="https://fonts.googleapis.com/css2?family=Marcellus&family=Noto+Sans:wght@400&family=Tenor+Sans&display=swap">
<style>
  :root {
    --brand-red: #6b0a0a;
    --brand-red-deep: #520606;
    --sky-top: #6fa9cf;
    --sky-mid: #a9cfe6;
    --haze: #d8e6ee;
    --city: #9aa9b3;
    --water: #7f9fb6;
    --panel-blue: rgba(150, 200, 226, 0.88);
    --panel-edge: #b7dbef;
    --tab-blue: #7fb2d6;
    --tab-blue-dark: #5f97c0;
    --login-blue: #6aa7cf;
    --nav-grey: #dedede;
    --white: #ffffff;
    --ink: #333333;
    --rule: #b5b5b5;
    --footer-dark: #2a2a2a;
  }
  * { box-sizing: border-box; margin: 0; padding: 0; }
  html, body { width: 1200px; height: 759px; overflow: hidden; }
  body { position: relative; font-family: "Noto Sans", Verdana, sans-serif; color: var(--ink); }

  .backdrop {
    position: absolute; inset: 0 0 9px 0;
    background: linear-gradient(180deg, var(--sky-top) 0%, var(--sky-mid) 38%, var(--haze) 62%, var(--city) 74%, var(--water) 100%);
  }
  .base-band { position: absolute; left: 0; right: 0; bottom: 0; height: 9px; background: var(--footer-dark); }

  .site-header {
    position: absolute; left: 153px; top: 0; width: 900px; height: 176px;
    background: rgba(255,255,255,0.96);
  }
  .brand { position: absolute; left: 12px; top: 8px; width: 78px; text-align: center; }
  .brand-square { width: 62px; height: 62px; margin: 0 auto 8px; background: var(--brand-red); }
  .brand-name { font-family: "Marcellus", serif; font-size: 19px; color: var(--brand-red); }

  .client-login {
    position: absolute; right: 11px; top: 13px; width: 84px; height: 30px;
    background: var(--login-blue); color: var(--white); font-size: 13px; line-height: 30px; text-align: center;
  }
  .main-nav { position: absolute; left: 357px; top: 140px; display: flex; gap: 4px; }
  .main-nav a {
    display: block; width: 102px; height: 36px; background: var(--nav-grey);
    font-family: "Marcellus", serif; font-size: 14px; line-height: 38px; text-align: center;
    color: var(--brand-red); text-decoration: none;
  }

  .strapline { position: absolute; left: 150px; top: 216px; }
  .strapline-main { font-family: "Tenor Sans", sans-serif; font-size: 49px; line-height: 1; color: var(--white); letter-spacing: 1px; }
  .strapline-sub { font-family: "Tenor Sans", sans-serif; font-size: 32px; line-height: 1; color: var(--brand-red); letter-spacing: 1px; }

  .service-panel {
    position: absolute; left: 659px; top: 248px; width: 391px; height: 244px;
    background: var(--panel-blue); border: 1px solid var(--panel-edge);
  }
  .service-tabs { position: absolute; left: 7px; top: 7px; display: flex; gap: 2px; }
  .service-tab {
    position: relative; width: 187px; height: 49px; padding: 6px 0 0 10px;
    background: linear-gradient(180deg, var(--tab-blue), var(--tab-blue-dark)); color: var(--white);
  }
  .service-tab.is-active { background: linear-gradient(180deg, #8cbfe0, #6ea5cc); border: 1px solid #d2ebf8; }
  .service-tab h3 { font-family: "Marcellus", serif; font-weight: 400; font-size: 17px; line-height: 1.1; color: #1d3350; }
  .service-tab p { font-size: 11px; }
  .service-tab svg { position: absolute; right: 12px; top: 16px; }
  .service-copy {
    position: absolute; left: 20px; top: 72px; width: 350px;
    font-size: 15.5px; line-height: 23px; color: var(--brand-red-deep);
  }
  .btn-learn {
    position: absolute; left: 20px; top: 189px; width: 112px; height: 32px;
    background: linear-gradient(180deg, #a31a1a, #6d0808); color: var(--white);
    font-size: 13.5px; line-height: 32px; padding-left: 9px;
  }

  .site-footer {
    position: absolute; left: 153px; top: 563px; width: 900px; height: 187px; background: var(--white);
  }
  .footer-col { position: absolute; top: 19px; }
  .footer-col h4 { font-weight: 400; font-size: 15.5px; color: var(--brand-red); margin-bottom: 6px; }
  .footer-blog { left: 12px; width: 258px; }
  .blog-item {
    position: relative; padding: 0 0 9px 12px; margin-bottom: 9px;
    font-size: 11.2px; line-height: 13px; color: var(--ink); border-bottom: 1px solid var(--rule);
  }
  .blog-item:last-child { border-bottom: 0; }
  .blog-item::before {
    content: ""; position: absolute; left: 2px; top: 2px;
    border-left: 5px solid var(--brand-red); border-top: 4px solid transparent; border-bottom: 4px solid transparent;
  }
  .more-link { color: var(--brand-red); font-size: 10px; text-decoration: underline; }
  .footer-download { left: 295px; width: 260px; }
  .footer-download p { font-size: 11.2px; line-height: 14.5px; padding-left: 2px; }
  .download-btn {
    position: absolute; left: 0; top: 126px; width: 246px; height: 48px; border-radius: 3px;
    background: linear-gradient(180deg, #8cbde0, #5b94c0); border: 1px solid #4f86b2;
    color: var(--white); font-size: 15px; font-weight: 700; line-height: 15px; padding: 9px 0 0 57px;
  }
  .download-btn .doc-square { position: absolute; left: 5px; top: 5px; width: 37px; height: 36px; background: #c9382a; }
  .footer-contact { left: 574px; width: 200px; }
  .footer-contact address { font-style: normal; font-size: 11.2px; line-height: 15px; padding-left: 2px; }
  .footer-contact .email { margin-top: 13px; }
  .copyright { margin-top: 17px; font-size: 10px; color: var(--brand-red); }
  .footer-brand { position: absolute; left: 817px; top: 17px; width: 70px; text-align: center; }
  .footer-brand .brand-square { width: 70px; height: 70px; margin-bottom: 10px; }
</style>
</head>
<body>
  <div class="backdrop" role="img" aria-label="Photograph of suspension bridge cables over a bay with a city skyline"></div>
  <div class="base-band"></div>

  <header class="site-header">
    <div class="brand">
      <div class="brand-square"></div>
      <div class="brand-name">Halvorn</div>
    </div>
    <a class="client-login">Client Login</a>
    <nav class="main-nav">
      <a>HOME</a><a>ABOUT US</a><a>SURVEYS</a><a>CONSULTING</a><a>BLOG</a>
    </nav>
  </header>

  <div class="strapline">
    <div class="strapline-main">FOCUSSED DATA</div>
    <div class="strapline-sub">is the key to success</div>
  </div>

  <section class="service-panel">
    <div class="service-tabs">
      <div class="service-tab is-active">
        <h3>SURVEYS</h3><p>Aliquam erat volutpat.</p>
        <svg width="16" height="10" viewBox="0 0 16 10"><path d="M0 0h16L8 9z" fill="#fff"/></svg>
      </div>
      <div class="service-tab">
        <h3>CONSULTING</h3><p>Aliquam erat volutpat.</p>
        <svg width="10" height="16" viewBox="0 0 10 16"><path d="M0 0v16l9-8z" fill="#fff"/></svg>
      </div>
    </div>
    <p class="service-copy">Lorem ipsum dolor sit amet, consectetur adipiscing elit. Morbi a purus vel sem accumsan varius eget ut erat. Class aptent taciti sociosqu ad litora torquent per conubia nostra, per inceptos himenaeos.</p>
    <a class="btn-learn">LEARN MORE</a>
  </section>

  <footer class="site-footer">
    <div class="footer-col footer-blog">
      <h4>BLOG</h4>
      <div class="blog-item">Lorem ipsum dolor sit amet, consectetur adipiscing elit. <span class="more-link">LEARN MORE</span></div>
      <div class="blog-item">Morbi a purus vel sem accumsan varius eget ut erat. <span class="more-link">LEARN MORE</span></div>
      <div class="blog-item">Class aptent taciti sociosqu ad litora torquent per conubia nostra. <span class="more-link">LEARN MORE</span></div>
    </div>
    <div class="footer-col footer-download">
      <h4>FREE Download</h4>
      <p>er inceptos himenaeos. Pellentesque habitant morbi tristique senectus et netus et malesuada fames ac turpis egestas. Aliquam erat volutpat. Maecenas dapibus</p>
      <a class="download-btn"><span class="doc-square"></span>RESEARCH REPORT +<br>SUPPORTING BLURB</a>
    </div>
    <div class="footer-col footer-contact">
      <h4>Contact Us</h4>
      <address>
        Halvorn<br>Suite 200 - 3870 Larchmere Rd. N.W.<br>Cityname, State Name<br>USA
        <div class="email">E-mail: contact@halvorn.com</div>
      </address>
      <div class="copyright">© 2011 Halvorn.com. All rights reserved</div>
    </div>
    <div class="footer-brand">
      <div class="brand-square"></div>
      <div class="brand-name">Halvorn</div>
    </div>
  </footer>
</body>
</html>
```